Willow Creek Gatherings Event Planning in need of a design!!

Event Planning company, does a variety of events. I like simple more rustic designs focused on almond blossoms. We are based out of Northern California, the heart of almond country. I would like to see colors in light pinks, beige, light browns, whites or creams. the final design should communicate rustic simplicity. Below are some pictures of Almond blossoms and design ideas I prefer the one called Tulip Grove. Thanks

Target Market(s)

Women in the mid twenties and older. They should be in the upper middle class in need of an amazing party design and coordinator

Industry/Entity Type

Event Planning

Contact Information for Business Card

Maren Lockwood 530-624-0295almondbaffairs@gmail.comalmondblossomaffairs.com

Font styles to use
Other font styles liked:
• Amatic SC

Requirements
Must have
• almond blossom
• my information
• simplicity
Nice to have
• rustic design
• vintage feel
• whimsical
Should not have
• i like pink but not over the top

```html
<!DOCTYPE html>
<html lang="en">
<head>
<meta charset="utf-8">
<title>Willow Creek Gatherings – Business Card</title>
<link rel="stylesheet" href="https://fonts.googleapis.com/css2?family=Jost:wght@400&family=Open+Sans:wght@400;600&display=swap">
<style>
  :root {
    --stage: #ecebe9;
    --card-front: #000000;
    --blossom-pink: #f08fc0;
    --leaf-green: #2fa56e;
    --ink-white: #ffffff;
    --photo-deep: #1c2740;
    --photo-mid: #3d4a63;
    --photo-light: #8a8f99;
  }
  * { margin: 0; padding: 0; box-sizing: border-box; }
  html, body { width: 1200px; height: 900px; overflow: hidden; }
  body {
    position: relative;
    background: var(--stage);
    font-family: "Open Sans", Arial, sans-serif;
  }
  .card {
    position: absolute;
    overflow: hidden;
    box-shadow: 0 6px 18px rgba(0,0,0,0.18);
  }
  .card--front {
    left: 238px; top: 62px; width: 555px; height: 342px;
    background: var(--card-front);
    text-align: center;
  }
  .card--back {
    left: 457px; top: 518px; width: 560px; height: 343px;
  }
  .brand-dot {
    display: block;
    margin: 0 auto;
    border-radius: 50%;
  }
  .card--front .brand-dot {
    width: 38px; height: 38px;
    margin-top: 56px;
    background: var(--blossom-pink);
  }
  .brand-name {
    font-family: "Jost", "Century Gothic", sans-serif;
    font-weight: 400;
    text-transform: uppercase;
    letter-spacing: 1.5px;
    line-height: 1.1;
  }
  .card--front .brand-name {
    margin-top: 24px;
    font-size: 27px;
    color: var(--blossom-pink);
  }
  .person-name {
    margin-top: 46px;
    font-weight: 600;
    font-size: 19px;
    color: var(--blossom-pink);
  }
  .contact-list {
    list-style: none;
    margin-top: 22px;
    color: var(--ink-white);
    font-size: 14.5px;
    line-height: 20px;
  }
  .contact-list li {
    display: flex;
    justify-content: center;
    align-items: center;
    gap: 9px;
  }
  .contact-icon { width: 11px; height: 11px; fill: var(--leaf-green); }
  .blossom-photo {
    position: absolute; inset: 0;
    background:
      radial-gradient(ellipse at 30% 70%, rgba(200,200,205,0.45), transparent 55%),
      radial-gradient(ellipse at 85% 40%, rgba(170,175,185,0.35), transparent 50%),
      linear-gradient(135deg, var(--photo-mid), var(--photo-deep) 60%, var(--photo-light));
  }
  .back-content {
    position: relative;
    text-align: center;
    color: var(--ink-white);
  }
  .card--back .brand-dot {
    width: 44px; height: 44px;
    margin-top: 92px;
    background: var(--ink-white);
  }
  .card--back .brand-name {
    margin-top: 34px;
    font-size: 32px;
    color: var(--ink-white);
  }
</style>
</head>
<body>

  <section class="card card--front" aria-label="Business card front">
    <span class="brand-dot"></span>
    <h1 class="brand-name">Willow Creek Gatherings</h1>
    <p class="person-name">Maren Lockwood</p>
    <ul class="contact-list">
      <li>
        <svg class="contact-icon" viewBox="0 0 24 24" aria-hidden="true"><path d="M6.6 10.8a15.1 15.1 0 0 0 6.6 6.6l2.2-2.2a1 1 0 0 1 1-.25 11.4 11.4 0 0 0 3.6.57 1 1 0 0 1 1 1V20a1 1 0 0 1-1 1A17 17 0 0 1 3 4a1 1 0 0 1 1-1h3.5a1 1 0 0 1 1 1c0 1.25.2 2.45.57 3.57a1 1 0 0 1-.25 1z"/></svg>
        530-817-4362
      </li>
      <li>
        <svg class="contact-icon" viewBox="0 0 24 24" aria-hidden="true"><path d="M2 5h20v14H2z M2 5l10 8 10-8" fill="var(--leaf-green)"/><path d="M3 6l9 7 9-7" stroke="#000" stroke-width="1.6" fill="none"/></svg>
        willowcgather@mailbox.test
      </li>
      <li>
        <svg class="contact-icon" viewBox="0 0 24 24" aria-hidden="true"><circle cx="12" cy="12" r="11"/><path d="M1 12h22M12 1c4 4 4 18 0 22M12 1c-4 4-4 18 0 22" stroke="#000" stroke-width="1.4" fill="none"/></svg>
        willowcreekgatherings.test
      </li>
    </ul>
  </section>

  <section class="card card--back" aria-label="Business card back">
    <div class="blossom-photo" role="img" aria-label="Photograph of white almond blossoms on branches against a dark blue sky"></div>
    <div class="back-content">
      <span class="brand-dot"></span>
      <h2 class="brand-name">Willow Creek Gatherings</h2>
    </div>
  </section>

</body>
</html>
```